Lumvra App | Pre-Launch Homepage

Dear designer,
Lumvra is a soon to be launched innovative & free social platform for collaborative addictions quitting.
We require a design for our pre-launch homepage that will elevate our basic wireframes to the next level.
We would like the wireframes to serve as a guideline only, and not as a final version of the design. If you have cool ideas - we would appreciate your creativity!
* This is a pre-launch website for a mobile app, and as such the design must be consistent with the general style, design and atmosphere of the app (see screenshot in the shared Drive link).
* We liked the style and feel of the following website: http://tandelhub.example/ - Please let's use it as a reference as well.
* The existing text in the wireframes is there just to represent a place for text. Copy will be edited by us after the design is done.
Please find the wireframes attached, and all relevant design assets and app screenshots in the following Drive shared link -
https://files.example-share.net/open?id=7KQ204RtP3mNxa8Y2Lb61H9cdVzQ
Thanks,
Reginald
Industry/Entity Type
Social
Number of Pages Required
1 page
Look and feel
Each slider illustrates characteristics of the customer's brand and the style your logo design should communicate.

```html
<!DOCTYPE html>
<html lang="en">
<head>
<meta charset="utf-8">
<title>Lumvra App | Pre-Launch Homepage</title>
<link href="https://fonts.googleapis.com/css2?family=Raleway:wght@200;300;400;600;700&family=Open+Sans:wght@400;600;700&display=swap" rel="stylesheet">
<style>
:root{
  --orange:#f7931e;
  --orange-deep:#ee7d0c;
  --amber:#ffb400;
  --brown-dark:#2b1d12;
  --brown:#4a3420;
  --blue:#2f9cf0;
  --blue-light:#6cc3ff;
  --white:#ffffff;
  --ink:#4b4b4b;
  --muted:#8a8a8a;
  --line:#d6d6d6;
  --paper:#f1f1f1;
  --device:#1e1e22;
  --icon-dark:#3c4250;
}
*{box-sizing:border-box;margin:0;padding:0}
html,body{width:1200px;height:3980px;overflow:hidden}
body{position:relative;background:var(--white);font-family:"Open Sans",Arial,sans-serif;color:var(--ink)}
.abs{position:absolute}
.center{text-align:center}

/* hero */
.hero{top:0;left:0;width:1200px;height:690px;background:radial-gradient(ellipse at 50% 40%,var(--brown) 0%,var(--brown-dark) 75%);clip-path:polygon(0 0,1200px 0,1200px 620px,0 690px)}
.brand{font-family:"Raleway",sans-serif;font-weight:700;color:var(--amber)}
.hero .brand{top:40px;left:0;width:1200px;font-size:66px;text-align:center}
.btn-contact{top:22px;left:925px;width:150px;height:44px;border-radius:22px;background:var(--amber);color:var(--brown-dark);font:600 15px "Open Sans",sans-serif;line-height:44px;text-align:center}
.tagline{top:220px;width:1200px;font:400 27px "Raleway",sans-serif;color:var(--amber)}
.hero-desc{top:285px;left:380px;width:440px;font-size:16px;line-height:24px;color:#e9ddd0}
.subscribe-box{top:350px;left:320px;width:560px;height:135px;background:rgba(0,0,0,.45)}
.subscribe-box h3{position:absolute;top:22px;width:100%;font:400 20px "Raleway",sans-serif;color:var(--white);text-align:center}
.field{height:42px;border-bottom:1px solid #bbb;color:#bbb;font-size:13px;line-height:42px;padding-left:6px}
.btn-pill{height:40px;border-radius:20px;background:var(--orange);color:var(--white);font:700 12px "Open Sans",sans-serif;line-height:40px;text-align:center;letter-spacing:.5px}
.device{border-radius:26px;background:var(--device);padding:14px}
.device .screen{width:100%;height:100%;border-radius:6px}
.chevron{width:56px;height:56px;border-radius:50%;background:var(--white);border:2px solid var(--line)}

/* features */
.feature{width:240px;height:255px;top:715px}
.feature.card{background:var(--white);box-shadow:0 2px 14px rgba(0,0,0,.15)}
.feature svg{position:absolute;top:20px;left:60px}
.feature h4{position:absolute;top:150px;width:100%;font:400 20px "Raleway",sans-serif;color:var(--ink);text-align:center}
.feature p{position:absolute;top:185px;left:20px;width:200px;font-size:12px;line-height:17px;color:var(--muted);text-align:center}

/* bands */
.band-title{font:200 60px "Raleway",sans-serif;color:var(--white)}
.band-text{font-size:15px;line-height:23px;color:var(--white)}
.band-text b{font-weight:700}
.fun{top:1000px;left:0;width:1200px;height:520px;background:linear-gradient(135deg,var(--blue-light),var(--blue) 60%,#1f86dc);clip-path:polygon(0 70px,1200px 0,1200px 520px,0 460px)}
.inspire{top:1450px;left:0;width:1200px;height:400px;background:linear-gradient(120deg,var(--orange-deep),var(--orange) 55%,var(--amber));clip-path:polygon(0 0,1200px 60px,1200px 340px,0 400px)}

/* achieve */
.section-title{font:300 50px "Raleway",sans-serif;color:var(--ink)}
.achieve-text{font-size:15px;line-height:23px;color:var(--ink)}
.point{width:220px;font-size:12px;line-height:18px;color:var(--muted)}
.point-icon{width:56px;height:56px}

/* coming soon */
.coming{top:2400px;left:0;width:1200px;height:470px;background:linear-gradient(160deg,#5ab8ff,var(--blue) 50%,#1c7fd6);clip-path:polygon(0 40px,1200px 0,1200px 400px,0 470px)}
.coming-title{top:2425px;width:1200px;font:300 46px "Raleway",sans-serif;color:var(--white);z-index:1}

/* download */
.store{height:50px;border-radius:25px;border:2px solid var(--line);font:600 15px "Open Sans",sans-serif;color:var(--muted);line-height:46px;padding-left:56px}
.store.primary{border-color:var(--orange);color:var(--orange)}
.store i{position:absolute;left:18px;top:11px;width:24px;height:24px;border-radius:50%;background:currentColor}

/* newsletter & footer */
.newsletter{top:3420px;left:0;width:1200px;height:210px;background:var(--paper)}
.footer{top:3620px;left:0;width:1200px;height:360px;background:var(--orange)}
.footer .brand{color:var(--white);font-size:54px}
.footer-links a{color:var(--white);font-size:14px;text-decoration:none;margin:0 16px}
.social{width:46px;height:46px;border-radius:50%;border:2px solid var(--white)}
</style>
</head>
<body>

<!-- Hero -->
<header class="abs hero">
  <div class="abs brand">Lumvra</div>
  <div class="abs btn-contact">Contact Us</div>
  <h2 class="abs tagline center">Become a Better Version of Yourself</h2>
  <p class="abs hero-desc center">Lumvra is a revolutionary &amp; free social platform for collaborative addictions quitting.</p>
  <div class="abs subscribe-box">
    <h3>Subscribe below for the beta release and updates.</h3>
    <div class="abs field" style="top:68px;left:30px;width:340px">Enter your email address</div>
    <div class="abs btn-pill" style="top:70px;left:385px;width:150px">LET ME KNOW!</div>
  </div>
  <div class="abs device" style="top:300px;left:-30px;width:260px;height:300px;transform:rotate(-8deg)" role="img" aria-label="Tablet showing the app start screen"><div class="screen" style="background:linear-gradient(160deg,#2d3b4d,#5a7aa0)"></div></div>
  <div class="abs device" style="top:170px;left:950px;width:200px;height:400px;transform:rotate(10deg);background:#eaeaea" role="img" aria-label="Phone showing the app profile screen"><div class="screen" style="background:linear-gradient(170deg,#3b3226,#8a6a40)"></div></div>
  <div class="abs" style="top:540px;left:560px;width:80px;height:50px;border-radius:6px;background:linear-gradient(#cfcfcf,#8e8e8e)" role="img" aria-label="Small app devices"></div>
</header>
<div class="abs chevron" style="top:637px;left:572px">
  <svg width="52" height="52" viewBox="0 0 52 52"><path d="M18 22l8 8 8-8" fill="none" stroke="#8a8a8a" stroke-width="3" stroke-linecap="round"/></svg>
</div>

<!-- Features -->
<section>
  <div class="abs feature card" style="left:60px">
    <svg width="120" height="120" viewBox="0 0 120 120"><circle cx="60" cy="60" r="56" fill="#fff" stroke="#f7931e" stroke-width="3"/><circle cx="60" cy="60" r="34" fill="none" stroke="#e53b2c" stroke-width="16"/><circle cx="60" cy="60" r="34" fill="none" stroke="#fff" stroke-width="16" stroke-dasharray="18 35.4"/></svg>
    <h4>Never be Alone</h4>
    <p>Forget what you know - Lumvra makes it fun to quit.</p>
  </div>
  <div class="abs feature" style="left:480px">
    <svg width="120" height="120" viewBox="0 0 120 120"><circle cx="60" cy="60" r="56" fill="#fff" stroke="#f7931e" stroke-width="3"/><polygon points="60,22 70,50 100,50 76,68 85,97 60,80 35,97 44,68 20,50 50,50" fill="#f5b81c"/></svg>
    <h4>Network Power</h4>
    <p>Forget what you know - Lumvra makes it fun to quit.</p>
  </div>
  <div class="abs feature" style="left:900px">
    <svg width="120" height="120" viewBox="0 0 120 120"><circle cx="60" cy="60" r="56" fill="#fff" stroke="#f7931e" stroke-width="3"/><circle cx="60" cy="60" r="28" fill="none" stroke="#6b6b6b" stroke-width="12" stroke-dasharray="8 6"/><circle cx="60" cy="60" r="16" fill="#8a8a8a"/></svg>
    <h4>Stay Motivated</h4>
    <p>Forget what you know - Lumvra makes it fun to quit.</p>
  </div>
</section>

<!-- Fun -->
<section class="abs fun">
  <div class="abs device" style="top:110px;left:140px;width:420px;height:290px;transform:rotate(-12deg);background:#f2f2f2" role="img" aria-label="Tablet showing the app campaign screen"><div class="screen" style="background:linear-gradient(150deg,#1c2a3a,#4d6b8a)"></div></div>
  <h2 class="abs band-title" style="top:100px;left:640px">Fun</h2>
  <p class="abs band-text" style="top:190px;left:640px;width:420px">Forget what you know – <b>Lumvra makes it fun to quit.</b> The battle between your good and bad demons comes to life in our <b>gamified approach</b> for managing your campaigns.</p>
  <p class="abs band-text" style="top:300px;left:640px;width:420px">Lumvra gives you the opportunity to <b>take an active role</b> in helping your network to <b>smash</b> your common addictions as a team. That's right, we converted the cessation process into a social game.</p>
</section>

<!-- Inspire -->
<section class="abs inspire">
  <h2 class="abs band-title" style="top:90px;left:60px">Inspire</h2>
  <p class="abs band-text" style="top:180px;left:60px;width:500px">One of the most important factors for successful quitting is the ability to <b>stay inspired</b> during the process.</p>
  <p class="abs band-text" style="top:250px;left:60px;width:500px">That's why we designed Lumvra as a platform where you can inspire and be inspired by a supportive network of awesome Lumvra heroes.</p>
  <div class="abs device" style="top:70px;left:650px;width:520px;height:270px;transform:rotate(-10deg);background:#f2f2f2" role="img" aria-label="Tablet showing the app community feed"><div class="screen" style="background:linear-gradient(150deg,#2a3a4c,#6a4a3a)"></div></div>
</section>
<div class="abs chevron" style="top:1832px;left:572px">
  <svg width="52" height="52" viewBox="0 0 52 52"><path d="M18 22l8 8 8-8" fill="none" stroke="#8a8a8a" stroke-width="3" stroke-linecap="round"/></svg>
</div>

<!-- Achieve -->
<section>
  <h2 class="abs section-title center" style="top:1900px;width:1200px">Achieve</h2>
  <p class="abs achieve-text center" style="top:1975px;left:300px;width:600px">Lumvra is built as a <b>pyramid of relationships</b> that makes use of the <b>Social Cognitive Theory</b>, to provide a powerful network of positive reinforcement.</p>
  <p class="abs achieve-text center" style="top:2040px;width:1200px">The bigger you make it the stronger you get.</p>

  <p class="abs point" style="top:2190px;left:110px;text-align:right">Lumvra is built as a pyramid of relationships that makes use of the Social Cognitive Theory.</p>
  <svg class="abs point-icon" style="top:2180px;left:345px" viewBox="0 0 56 56"><circle cx="28" cy="28" r="26" fill="#fff" stroke="#d6d6d6" stroke-width="2"/><circle cx="28" cy="28" r="17" fill="#3c4250"/><ellipse cx="28" cy="28" rx="7" ry="17" fill="none" stroke="#9fb4cc" stroke-width="1.5"/><path d="M11 28h34M14 20h28M14 36h28" stroke="#9fb4cc" stroke-width="1.5"/></svg>
  <p class="abs point" style="top:2320px;left:110px;text-align:right">Lumvra is built as a pyramid of relationships that makes use of the Social Cognitive Theory.</p>
  <svg class="abs point-icon" style="top:2310px;left:345px" viewBox="0 0 56 56"><circle cx="28" cy="28" r="26" fill="#fff" stroke="#f7931e" stroke-width="2"/><rect x="14" y="24" width="18" height="10" rx="5" transform="rotate(-45 23 29)" fill="none" stroke="#6b6b6b" stroke-width="3"/><rect x="24" y="22" width="18" height="10" rx="5" transform="rotate(-45 33 27)" fill="none" stroke="#6b6b6b" stroke-width="3"/></svg>

  <svg class="abs point-icon" style="top:2180px;left:800px" viewBox="0 0 56 56"><circle cx="28" cy="28" r="26" fill="#fff" stroke="#d6d6d6" stroke-width="2"/><path d="M19 15h18v8a9 9 0 0 1-18 0z" fill="#3c4250"/><path d="M19 18h-5a5 5 0 0 0 5 7M37 18h5a5 5 0 0 1-5 7" fill="none" stroke="#3c4250" stroke-width="2"/><rect x="26" y="31" width="4" height="6" fill="#3c4250"/><rect x="20" y="37" width="16" height="4" fill="#3c4250"/></svg>
  <p class="abs point" style="top:2190px;left:870px">Lumvra is built as a pyramid of relationships that makes use of the Social Cognitive Theory.</p>
  <svg class="abs point-icon" style="top:2310px;left:800px" viewBox="0 0 56 56"><circle cx="28" cy="28" r="26" fill="#fff" stroke="#f7931e" stroke-width="2"/><path d="M14 24h28l-4 16H18z" fill="none" stroke="#3c4250" stroke-width="2.5" stroke-linejoin="round"/><path d="M21 24l5-9M35 24l-5-9M22 28v8M28 28v8M34 28v8" stroke="#3c4250" stroke-width="2"/></svg>
  <p class="abs point" style="top:2320px;left:870px">Lumvra is built as a pyramid of relationships that makes use of the Social Cognitive Theory.</p>

  <div class="abs device" style="top:2090px;left:515px;width:170px;height:300px;border-radius:28px;padding:40px 11px;z-index:2" role="img" aria-label="Phone showing the app relationship pyramid"><div class="screen" style="background:linear-gradient(180deg,#2a2f38,#4a3c2a)"></div></div>
</section>

<!-- Coming soon -->
<section class="abs coming"></section>
<h2 class="abs coming-title center">Coming Soon</h2>
<div class="abs device" style="top:2495px;left:515px;width:170px;height:320px;border-radius:28px;padding:42px 11px" role="img" aria-label="Phone showing the app home screen"><div class="screen" style="background:linear-gradient(180deg,#2b2f36,#53442e)"></div></div>
<svg class="abs" style="top:2820px;left:250px" width="700" height="110" viewBox="0 0 700 110">
  <path d="M140 10 Q80 50 40 90" fill="none" stroke="#9a9a9a" stroke-width="2"/><path d="M40 90 l4 -14 M40 90 l14 -4" stroke="#9a9a9a" stroke-width="2"/>
  <path d="M560 20 Q620 50 670 90" fill="none" stroke="#9a9a9a" stroke-width="2"/><path d="M670 90 l-14 -2 M670 90 l-2 -14" stroke="#9a9a9a" stroke-width="2"/>
</svg>

<!-- Download -->
<section>
  <h2 class="abs center" style="top:3120px;width:1200px;font:400 40px 'Raleway',sans-serif;color:var(--ink)">Download Our App</h2>
  <p class="abs center" style="top:3185px;width:1200px;font-size:13px;color:var(--muted)">Choose your native platform and download the app.</p>
  <div class="abs store primary" style="top:3245px;left:215px;width:230px"><i></i>Playfield Store</div>
  <div class="abs store" style="top:3245px;left:480px;width:230px"><i></i>Appora Store</div>
  <div class="abs store" style="top:3245px;left:745px;width:240px"><i></i>Panebox Store</div>
</section>

<!-- Newsletter -->
<section class="abs newsletter">
  <h2 class="abs center" style="top:42px;width:1200px;font:400 26px 'Raleway',sans-serif;color:var(--ink)">Subscribe To Newsletter</h2>
  <p class="abs center" style="top:84px;width:1200px;font-size:12px;color:var(--muted)">Subscribe below for the beta release and updates.</p>
  <div class="abs field" style="top:118px;left:350px;width:340px;color:#aaa;border-color:#c8c8c8">Enter your email address</div>
  <div class="abs btn-pill" style="top:120px;left:705px;width:140px">LET ME KNOW!</div>
</section>

<!-- Footer -->
<footer class="abs footer">
  <svg class="abs" style="top:-22px;left:90px" width="44" height="22" viewBox="0 0 44 22"><polygon points="0,22 22,0 44,22" fill="#f7931e"/></svg>
  <div class="abs brand center" style="top:40px;width:1200px">Lumvra</div>
  <nav class="abs footer-links center" style="top:125px;width:1200px"><a href="#">Contact Us</a><a href="#">T&amp;Cs</a><a href="#">Privacy Policy</a></nav>
  <div class="abs social" style="top:185px;left:507px"></div>
  <div class="abs social" style="top:185px;left:577px"></div>
  <div class="abs social" style="top:185px;left:647px"></div>
  <div class="abs" style="top:268px;left:0;width:1200px;height:1px;background:rgba(255,255,255,.35)"></div>
  <p class="abs center" style="top:300px;width:1200px;font-size:13px;color:var(--white)">© 2015 Lumvra Inc. All Rights Reserved.</p>
</footer>

</body>
</html>
```